Business Card Design - Amberfield Court

We are looking at a new design for our business cards that has a modern and professional look. We run a residential aged care facility focussing on the care of residents. The cards will be used for potential clients, consultants and business opportunities in this sector. Blue and white is our main colours and would to see these colours incorporated in the design.
Industry/Entity Type
Business
Contact Information for Business Card
Amberfield Court, Darren Walsh, dwalsh@amberfieldcourt.com.au, Finance Manager, 0472 639 208, BCom, 37 Marrabel Crescent, Brindle Vale, Qld 4093.
Look and feel
Each slider illustrates characteristics of the customer's brand and the style your logo design should communicate.

```html
<!DOCTYPE html>
<html lang="en">
<head>
<meta charset="utf-8">
<title>Amberfield Court – Business Card</title>
<link rel="stylesheet" href="https://fonts.googleapis.com/css2?family=Oswald:wght@400&family=Open+Sans:wght@400&display=swap">
<style>
  :root {
    --brand-blue: #4f7a93;
    --brand-taupe: #a99d96;
    --ink: #333333;
    --card: #ffffff;
    --backdrop: #e8e5e2;
  }
  * { margin: 0; padding: 0; box-sizing: border-box; }
  html, body { width: 1200px; height: 1000px; overflow: hidden; }
  body { background: var(--backdrop); position: relative; font-family: "Open Sans", sans-serif; color: var(--ink); }

  .card {
    position: absolute; left: 236px; width: 728px; height: 416px;
    background: var(--card); overflow: hidden;
    box-shadow: 0 2px 8px rgba(0,0,0,0.12);
  }
  .card--front { top: 72px; }
  .card--back { top: 512px; }

  .brand { display: flex; align-items: center; gap: 12px; position: absolute; }
  .brand__dot { width: 22px; height: 22px; border-radius: 50%; background: var(--brand-blue); }
  .brand__name {
    font-family: "Oswald", sans-serif; font-weight: 400; color: var(--brand-blue);
    letter-spacing: 2px; text-transform: uppercase; white-space: nowrap;
  }
  .card--front .brand { left: 0; right: 0; top: 212px; justify-content: center; }
  .card--front .brand__name { font-size: 30px; }
  .card--back .brand { left: 72px; top: 212px; }
  .card--back .brand__name { font-size: 27px; }

  .front__web {
    position: absolute; left: 0; right: 0; top: 354px; text-align: center;
    font-size: 15px; letter-spacing: 0.2px;
  }

  .contact { position: absolute; left: 381px; top: 86px; }
  .contact__name {
    font-family: "Oswald", sans-serif; font-size: 21px; color: var(--brand-blue);
    text-transform: uppercase; letter-spacing: 0.5px; line-height: 1.2;
  }
  .contact__role { font-size: 15px; margin-top: 3px; }
  .contact__rule {
    width: 80px; height: 2px; margin: 9px 0 12px;
    background: linear-gradient(to right, var(--ink), rgba(51,51,51,0));
  }
  .contact__address { font-size: 15px; line-height: 22px; font-style: normal; }
  .contact__list { list-style: none; margin-top: 12px; }
  .contact__item { display: flex; align-items: center; gap: 8px; font-size: 15px; line-height: 23px; }
  .contact__icon { width: 12px; height: 12px; flex: none; fill: var(--brand-blue); }

  .swoosh { position: absolute; left: 0; bottom: 0; width: 728px; height: 416px; }
</style>
</head>
<body>
  <section class="card card--front" aria-label="Card front">
    <div class="brand">
      <span class="brand__dot"></span>
      <span class="brand__name">Amberfield Court</span>
    </div>
    <p class="front__web">www.amberfieldcourt.com.au</p>
  </section>

  <section class="card card--back" aria-label="Card back">
    <svg class="swoosh" viewBox="0 0 728 416" aria-hidden="true">
      <path d="M0,330 C60,372 200,386 330,386 C200,393 60,386 0,368 Z" fill="var(--brand-taupe)"/>
      <path d="M0,362 C80,390 240,396 400,376 C520,361 640,336 728,312 L728,416 L0,416 Z" fill="var(--brand-blue)"/>
    </svg>

    <div class="brand">
      <span class="brand__dot"></span>
      <span class="brand__name">Amberfield Court</span>
    </div>

    <div class="contact">
      <h1 class="contact__name">Darren Walsh</h1>
      <p class="contact__role">Finance Manager</p>
      <div class="contact__rule"></div>
      <address class="contact__address">37 Marrabel Crescent,<br>Brindle Vale, Qld 4093</address>
      <ul class="contact__list">
        <li class="contact__item">
          <svg class="contact__icon" viewBox="0 0 12 12"><path d="M2.5 0.5 L4.5 0.5 L5.2 3.2 L3.8 4.3 C4.5 5.8 6 7.4 7.6 8.1 L8.7 6.8 L11.5 7.5 L11.5 9.6 C11.5 10.8 10.6 11.5 9.5 11.4 C4.8 10.9 1.1 7.2 0.6 2.5 C0.5 1.4 1.3 0.5 2.5 0.5 Z"/></svg>
          <span>0472 639 208</span>
        </li>
        <li class="contact__item">
          <svg class="contact__icon" viewBox="0 0 12 12"><path d="M0 2 L12 2 L12 10 L0 10 Z M0.8 2.6 L6 6.6 L11.2 2.6" stroke="#fff" stroke-width="0.9"/></svg>
          <span>dwalsh@amberfieldcourt.com.au</span>
        </li>
        <li class="contact__item">
          <svg class="contact__icon" viewBox="0 0 12 12" fill="none" style="fill:none;stroke:var(--brand-blue);stroke-width:1"><circle cx="6" cy="6" r="5.3"/><ellipse cx="6" cy="6" rx="2.3" ry="5.3"/><path d="M0.7 6 H11.3 M1.6 3.3 H10.4 M1.6 8.7 H10.4"/></svg>
          <span>www.amberfieldcourt.com.au</span>
        </li>
      </ul>
    </div>
  </section>
</body>
</html>
```